BrimFalcon Business Cards

We have a defined brand. Please visit our website to get a feel for the product and the color pallets. www.brimfalcon-example.com

We need an updated, world class business card design. (See the attached existing card design). Please utilize BOTH sides of the card as shown and be creative with the layout. I do want the horse head icon to be positioned as it is with the existing card.

The remainder of the layout can be customized and I also want it vertically oriented.

Attached are the logo files and please use the colors as follows:
Green - #A5CE39
Tan - #CDBD99
Black

Feel free to play with the colors.

```html
<!DOCTYPE html>
<html lang="en">
<head>
<meta charset="utf-8">
<title>BrimFalcon Business Cards</title>
<link rel="stylesheet" href="https://fonts.googleapis.com/css2?family=Roboto:wght@400;500;700&family=Barlow+Semi+Condensed:wght@600&display=swap">
<style>
  :root {
    --green: #a5ce39;
    --green-dark: #5d8a1c;
    --black: #0d0d0d;
    --white: #ffffff;
    --stage: #3b3b3b;
  }
  * { margin: 0; padding: 0; box-sizing: border-box; }
  html, body { width: 1200px; height: 1108px; overflow: hidden; }
  body {
    background: var(--stage);
    font-family: "Roboto", Arial, sans-serif;
    display: flex;
    align-items: center;
    justify-content: center;
    gap: 80px;
  }
  .card {
    position: relative;
    width: 400px;
    height: 660px;
    border-radius: 26px;
    overflow: hidden;
  }
  /* Front */
  .card-front { background: var(--white); }
  .front-base {
    position: absolute;
    left: 0; top: 0;
    width: 400px; height: 660px;
  }
  .brand {
    position: absolute;
    top: 150px;
    left: 0; right: 0;
    display: flex;
    align-items: center;
    justify-content: center;
    gap: 10px;
    font-size: 38px;
    font-weight: 700;
    color: var(--black);
    letter-spacing: 0.5px;
  }
  .brand-dot {
    width: 36px; height: 36px;
    border-radius: 50%;
    background: var(--black);
  }
  .details {
    position: absolute;
    right: 40px;
    top: 400px;
    text-align: right;
    color: var(--white);
  }
  .person-name {
    font-size: 32px;
    font-weight: 700;
    color: var(--green);
    text-transform: uppercase;
    line-height: 1;
  }
  .person-title {
    font-size: 17px;
    font-weight: 500;
    color: var(--green);
    margin-top: 4px;
  }
  .company {
    font-size: 17px;
    line-height: 23px;
    margin-top: 14px;
  }
  .contacts {
    list-style: none;
    margin-top: 16px;
    font-size: 17px;
    line-height: 25px;
  }
  .contacts li {
    display: flex;
    align-items: center;
    justify-content: flex-end;
    gap: 8px;
  }
  .contacts svg { width: 13px; height: 13px; flex: none; }
  /* Back */
  .card-back { background: var(--green); }
  .mark-shape {
    position: absolute;
    left: 80px;
    top: 170px;
    width: 240px;
    height: 240px;
    border-radius: 50%;
    background: var(--black);
  }
  .tagline {
    position: absolute;
    left: 0; right: 0;
    bottom: 70px;
    text-align: center;
    font-family: "Barlow Semi Condensed", Arial, sans-serif;
    font-weight: 600;
    font-size: 30px;
    color: var(--black);
  }
</style>
</head>
<body>
  <section class="card card-front">
    <svg class="front-base" viewBox="0 0 400 660" aria-hidden="true">
      <defs>
        <linearGradient id="swoosh" x1="0" y1="0" x2="1" y2="0">
          <stop offset="0" stop-color="#5d8a1c"/>
          <stop offset="0.6" stop-color="#a5ce39"/>
          <stop offset="1" stop-color="#c9e36a"/>
        </linearGradient>
      </defs>
      <path d="M0 330 C40 375 170 380 400 345 L400 660 L0 660 Z" fill="#0d0d0d"/>
      <path d="M0 322 C40 372 170 376 400 340 L400 348 C170 386 38 382 0 340 Z" fill="url(#swoosh)"/>
    </svg>
    <div class="brand"><span class="brand-dot"></span>BrimFalcon</div>
    <div class="details">
      <div class="person-name">Dana Mercer</div>
      <div class="person-title">President &amp; CEO</div>
      <div class="company">BrimFalcon Labs LLC<br>Northfield, Saskatchewan<br>Canada</div>
      <ul class="contacts">
        <li>306.555.0147
          <svg viewBox="0 0 16 16"><path d="M3 1l3 3-1.6 2a9 9 0 0 0 5.6 5.6L12 10l3 3-2 2C6 15 1 10 1 3z" fill="#a5ce39"/></svg></li>
        <li>dana@brimfalcon-example.com
          <svg viewBox="0 0 16 16"><rect x="1" y="3" width="14" height="10" fill="#a5ce39"/><path d="M1 3l7 6 7-6" fill="none" stroke="#0d0d0d" stroke-width="1.5"/></svg></li>
        <li>www.brimfalconlabs-example.com
          <svg viewBox="0 0 16 16"><circle cx="8" cy="8" r="7" fill="#a5ce39"/></svg></li>
      </ul>
    </div>
  </section>

  <section class="card card-back">
    <div class="mark-shape"></div>
    <div class="tagline">Movement Redesigned</div>
  </section>
</body>
</html>
```